Pebblebrook Plots - Online-only garden installation company

Online-only garden installation company. Our demographic is middle aged / suburban women, and we anticipate Facebook driving traffic to this website, as well as referrals from garden centers. The website must be very simple in design and function.

All orders will be placed through the website, including size of garden (3 options), location in yard, payment, and scheduling of installation date.

The website should employ a 3 step process:

Step 1: Select garden size. Either an 4' X 4', 8' X 4', or 12' X 4'.

Step 2: Select a location. We would like to use google maps to look up a US address, then "drag and drop" one of the garden sizes from step 1 to the location the customer would like us to install the garden at their home.

Step 3: Pick an installation date and pay. Using an online calendar the customer will pick a date, and then pay for the installation via credit card.

The website will be linked to an email account, PebblebrookPlots@mailvale.com to inform us of orders placed.

Target Market(s)

Our demographic is middle aged / suburban women, and we anticipate Facebook driving traffic to this website, as well as referrals from garden centers.

Industry/Entity Type

Coding

Number of Pages Required

Requirements
Must have
• Scheduling and payment options.

```html
<!DOCTYPE html>
<html lang="en">
<head>
<meta charset="utf-8">
<title>Pebblebrook Plots – Garden Installation</title>
<link rel="stylesheet" href="https://fonts.googleapis.com/css2?family=Alfa+Slab+One&family=Glegoo&family=Roboto+Slab:wght@400&family=Ubuntu:wght@400;500&display=swap">
<style>
  :root {
    --leaf: #5f9a1d;
    --leaf-line: #6ea82c;
    --carrot: #e0582a;
    --carrot-dark: #b8401b;
    --white: #ffffff;
    --ink: #555555;
    --field-icon: #d7d7d7;
    --panel: rgba(8, 8, 6, 0.78);
    --panel-line: rgba(255, 255, 255, 0.28);
  }
  * { box-sizing: border-box; margin: 0; padding: 0; }
  html, body { width: 1200px; height: 881px; overflow: hidden; }
  body { position: relative; font-family: "Ubuntu", sans-serif; color: var(--white); background: #2a2419; }

  .hero-photo {
    position: absolute; inset: 0;
    background:
      radial-gradient(ellipse at 55% 40%, rgba(240, 214, 150, 0.55) 0, rgba(240, 214, 150, 0) 22%),
      radial-gradient(ellipse at 22% 40%, rgba(214, 140, 60, 0.7) 0, rgba(214, 140, 60, 0) 18%),
      radial-gradient(ellipse at 88% 30%, rgba(110, 150, 50, 0.75) 0, rgba(110, 150, 50, 0) 26%),
      radial-gradient(ellipse at 20% 20%, rgba(220, 225, 215, 0.5) 0, rgba(220, 225, 215, 0) 20%),
      linear-gradient(180deg, #4d6a2c 0%, #5a5034 45%, #3a2c1f 70%, #22190f 100%);
  }

  .site-header {
    position: absolute; left: 0; top: 0; width: 1200px; height: 75px;
    background: var(--leaf);
  }
  .brand {
    position: absolute; left: 74px; top: 0; width: 152px; height: 145px;
    background: var(--white);
    display: flex; align-items: center; justify-content: center; text-align: center;
    font-family: "Roboto Slab", serif; font-size: 17px; line-height: 1.15; color: var(--carrot-dark);
  }
  .header-nav { position: absolute; right: 0; top: 0; height: 75px; display: flex; }
  .nav-item {
    height: 75px; border-left: 1px solid var(--leaf-line);
    display: flex; align-items: center; justify-content: center; gap: 10px;
  }
  .nav-icon { width: 80px; }
  .nav-login { width: 248px; justify-content: flex-start; padding-left: 30px; font-size: 14px; font-weight: 500; }

  .hero-heading { position: absolute; left: 0; top: 300px; width: 1200px; text-align: center; }
  .hero-title {
    font-family: "Alfa Slab One", serif; font-size: 40px; letter-spacing: 1px; font-weight: 400;
    line-height: 50px; text-shadow: 0 2px 6px rgba(0,0,0,.35);
  }
  .hero-ribbon { position: relative; display: inline-block; margin-top: 2px; width: 388px; height: 25px; }
  .hero-ribbon svg { position: absolute; inset: 0; }
  .hero-ribbon span {
    position: relative; font-family: "Roboto Slab", serif; font-size: 19px; line-height: 25px;
  }

  .order-panel {
    position: absolute; left: 113px; top: 592px; width: 974px; height: 203px;
    background: var(--panel); padding: 10px;
  }
  .order-frame { width: 100%; height: 100%; border: 1px solid var(--panel-line); position: relative; }
  .order-title {
    position: absolute; top: 28px; width: 100%; text-align: center;
    font-family: "Glegoo", serif; font-size: 31px; font-weight: 400;
  }
  .order-fields { position: absolute; left: 36px; top: 100px; display: flex; gap: 9px; }
  .field {
    width: 243px; height: 46px; background: var(--white); border-radius: 2px;
    display: flex; align-items: center; justify-content: space-between; padding: 3px 3px 3px 13px;
    font-size: 14px; color: var(--ink);
  }
  .field-icon {
    width: 43px; height: 40px; background: var(--field-icon);
    display: flex; align-items: center; justify-content: center;
  }
  .search-button {
    width: 127px; height: 46px; margin-left: 0; background: var(--carrot); border-radius: 2px;
    display: flex; align-items: center; justify-content: center; gap: 10px;
    font-size: 16px; font-weight: 500;
  }

  .site-footer {
    position: absolute; left: 0; top: 841px; width: 1200px; text-align: center; font-size: 14px;
    color: #eeeeee;
  }
</style>
</head>
<body>
  <div class="hero-photo" role="img" aria-label="Gloved hands planting a pot of cream primroses in dark soil, with daffodils, white and blue flowers and a wooden fence behind"></div>

  <header class="site-header">
    <div class="brand">Pebblebrook<br>Plots</div>
    <nav class="header-nav">
      <div class="nav-item nav-icon" aria-label="Search">
        <svg width="26" height="26" viewBox="0 0 26 26" fill="none" stroke="#fff" stroke-width="1.8"><circle cx="11" cy="11" r="9"/><path d="M17.5 17.5l7 7"/></svg>
      </div>
      <div class="nav-item nav-icon" aria-label="Cart">
        <svg width="28" height="24" viewBox="0 0 28 24" fill="none" stroke="#fff" stroke-width="1.6"><path d="M1 2h4l3 14h15l3-10H7"/><path d="M9 9h15M10 12.5h12"/><circle cx="11" cy="20.5" r="1.8"/><circle cx="21" cy="20.5" r="1.8"/></svg>
      </div>
      <div class="nav-item nav-login">
        <svg width="22" height="26" viewBox="0 0 22 26" fill="none" stroke="#fff" stroke-width="1.6"><circle cx="11" cy="8" r="6"/><path d="M1 25c0-6 4.5-9.5 10-9.5s10 3.5 10 9.5z"/></svg>
        LOGIN / SIGN UP
      </div>
    </nav>
  </header>

  <section class="hero-heading">
    <h1 class="hero-title">PEBBLEBROOK PLOTS</h1>
    <div class="hero-ribbon">
      <svg width="388" height="25" viewBox="0 0 388 25"><polygon points="0,0 40,0 40,25 0,25 8,12.5" fill="var(--carrot-dark)"/><polygon points="388,0 348,0 348,25 388,25 380,12.5" fill="var(--carrot-dark)"/><polygon points="32,0 356,0 348,25 40,25" fill="var(--carrot)"/></svg>
      <span>Only Garden Installation Company</span>
    </div>
  </section>

  <section class="order-panel">
    <div class="order-frame">
      <h2 class="order-title">Order Now Garden Installation Today</h2>
      <div class="order-fields">
        <div class="field">Select garden size
          <span class="field-icon"><svg width="10" height="8" viewBox="0 0 10 8"><path d="M0 0h10L5 8z" fill="#777"/></svg></span>
        </div>
        <div class="field">Select a location
          <span class="field-icon"><svg width="22" height="22" viewBox="0 0 22 22" fill="none" stroke="#666" stroke-width="1.6"><circle cx="11" cy="11" r="7"/><circle cx="11" cy="11" r="3" fill="#666"/><path d="M11 1v3M11 18v3M1 11h3M18 11h3"/></svg></span>
        </div>
        <div class="field">Pick an installation date
          <span class="field-icon"><svg width="20" height="20" viewBox="0 0 20 20" fill="none" stroke="#666" stroke-width="1.4"><rect x="1" y="3" width="18" height="16"/><path d="M1 7h18M5 1v4M15 1v4"/><path d="M4 10h2M9 10h2M14 10h2M4 13h2M9 13h2M14 13h2M4 16h2M9 16h2" stroke-width="1.6"/></svg></span>
        </div>
        <div class="search-button">
          <svg width="22" height="22" viewBox="0 0 22 22" fill="none" stroke="#fff" stroke-width="1.8"><circle cx="9.5" cy="9.5" r="7.5"/><path d="M15 15l6 6"/></svg>
          SEARCH
        </div>
      </div>
    </div>
  </section>

  <footer class="site-footer">© 2017 Pebblebrook Plots.&nbsp; Terms of Use | Privacy Policy | Sitemap</footer>
</body>
</html>
```